Brisk. Technology Logistics Software platform.

A modern looking and feeling website for a logistics software platform.
We connect retailers or wholesale parcel distributors to worldwide delivery solutions.
Methods tend to be road and air transport to final mile courier companies and post offices all over the world.
Our platform is for ecommerce distribution. A customer uses BRISK to enable them to connect to worldwide companies who will track and trace the delivery of their goods.

Target Market(s)

Onllne retailers. Markert Places such as Vendora and Tradelo. Wholesale third party logistics and packaging companies. Delivery companies based in the UK looking to expand overseas.

Number of Pages Required

5+ page

Font styles to use
Sans Serif

Colors
aaaaaa
dbdbdb
e6e6e6
c4c4c4
cbcbcb
c9c9c9
ec1f27
3176b5
0355a3

Requirements
Must have
• Landing Page.
• What we do.
• Who we are.
• Modules.
• Testimonies (password protected)
• Contact us.
• Interactive for mobile operating systems.
• Scrolling website.
• Short stock video showing on key pages.
• Very well polished fonts and buttons. A sharp and well executed website is required.
• Simplicity in feeling.
• To the point on message.
• Refined wording and copyrighting / messaging
• A link to our sub brand and product Brisk Parcels
• Capture interest so people read further.
Nice to have
• A polished video to explain what we do on landing page. Clipmarrow.net have some good options but not sure how professional they will look.
Should not have
• Bad graphics and colours.
• Not lots of clicks. Less as possible
• Complex message

```html
<!DOCTYPE html>
<html lang="en">
<head>
<meta charset="utf-8">
<title>Brisk. Technology – Website Pages</title>
<link rel="stylesheet" href="https://fonts.googleapis.com/css2?family=Lato:wght@400;700&family=Oswald:wght@400&family=Poppins:wght@400&display=swap">
<style>
  :root {
    --board: #9e9e9e;
    --red: #ec1f27;
    --white: #ffffff;
    --ink: #2b2b2b;
    --grey-head: #7a7a7a;
    --footer: #222222;
    --footer-text: #e6e6e6;
    --icon-ring: #d9d9d9;
  }
  * { margin: 0; padding: 0; box-sizing: border-box; }
  html, body { width: 1200px; height: 888px; overflow: hidden; }
  body { background: var(--board); position: relative; font-family: 'Lato', sans-serif; }

  .page { position: absolute; top: 104px; width: 535px; overflow: hidden;
    box-shadow: 0 6px 18px rgba(0,0,0,0.35); }
  .page--home { left: 53px; height: 681px; background: var(--white); }
  .page--focus { left: 612px; height: 410px; background: var(--footer); }

  .hero { position: absolute; left: 0; top: 0; width: 535px; }
  .page--home .hero { height: 308px;
    background:
      radial-gradient(ellipse 220px 120px at 300px 120px, rgba(190,205,225,0.45) 0%, rgba(190,205,225,0) 100%),
      radial-gradient(ellipse 160px 90px at 420px 150px, rgba(150,180,210,0.35) 0%, rgba(150,180,210,0) 100%),
      radial-gradient(ellipse 200px 110px at 110px 250px, rgba(120,100,80,0.45) 0%, rgba(120,100,80,0) 100%),
      linear-gradient(180deg, #27303f 0%, #3d4b60 30%, #4f5a68 55%, #45474b 78%, #2f2d2b 100%); }
  .page--focus .hero { height: 312px;
    background:
      radial-gradient(ellipse 230px 90px at 300px 100px, rgba(220,150,70,0.45) 0%, rgba(220,150,70,0) 100%),
      radial-gradient(ellipse 170px 80px at 460px 180px, rgba(70,110,170,0.40) 0%, rgba(70,110,170,0) 100%),
      radial-gradient(ellipse 150px 70px at 80px 190px, rgba(60,90,140,0.35) 0%, rgba(60,90,140,0) 100%),
      linear-gradient(180deg, #2a2624 0%, #4b3c2e 35%, #4a4037 60%, #403c3a 80%, #333130 100%); }
  .hero::after { content: ""; position: absolute; inset: 0;
    background: radial-gradient(ellipse at 50% 50%, rgba(0,0,0,0) 45%, rgba(0,0,0,0.35) 100%); }
  .hero > * { z-index: 1; }

  .brand { position: absolute; display: flex; align-items: center; gap: 6px;
    font-family: 'Lato', sans-serif; font-weight: 700; color: var(--white); }
  .brand__dot { width: 26px; height: 26px; border-radius: 50%; background: var(--red); }
  .brand__name { font-size: 26px; line-height: 1; }
  .page--home .brand { left: 64px; top: 25px; }
  .page--focus .brand { left: 50%; top: 65px; transform: translateX(-50%); }

  .nav { position: absolute; left: 224px; top: 33px; display: flex; gap: 12px; }
  .nav a { color: var(--white); text-decoration: none; font-weight: 700; font-size: 8.6px; letter-spacing: 0.1px; }

  .play { position: absolute; width: 36px; height: 36px; }
  .page--home .play { left: 249px; top: 123px; }
  .page--focus .play { left: 249px; top: 113px; }

  .slide-arrow { position: absolute; top: 145px; }
  .slide-arrow--prev { left: 52px; }
  .slide-arrow--next { left: 470px; }

  .hero__title { position: absolute; left: 0; width: 100%; text-align: center;
    font-family: 'Oswald', sans-serif; font-weight: 400; color: var(--white); }
  .page--home .hero__title { top: 169px; font-size: 17.5px; line-height: 24px; }
  .page--focus .hero__title { top: 156px; font-size: 23px; line-height: 30px; }

  .hero__copy { position: absolute; left: 0; top: 0; width: 100%; height: 100%; text-align: center;
    color: var(--white); font-size: 7.8px; }
  .hero__copy p { position: absolute; left: 0; width: 100%; line-height: 12px; }
  .hero__copy p:nth-child(1) { top: 194px; }
  .hero__copy p:nth-child(2) { top: 211px; }
  .hero__copy p:nth-child(3) { top: 226px; }
  .hero__copy p:nth-child(4) { top: 244px; }

  .wave { position: absolute; left: 0; width: 535px; display: block; z-index: 2; }

  .welcome { position: absolute; left: 0; top: 300px; width: 100%; text-align: center; z-index: 3; }
  .welcome__mark { width: 38px; height: 38px; border-radius: 50%; background: var(--red);
    margin: 3px auto 0; }
  .welcome__title { margin-top: 16px; font-size: 17.5px; font-weight: 700; color: var(--grey-head); letter-spacing: 0.2px; }
  .welcome__title span { color: var(--red); }
  .welcome__text { margin: 10px auto 0; width: 356px; font-size: 7.6px; line-height: 14.2px; color: var(--ink); }
  .welcome__text p + p { margin-top: 4px; }
  .welcome__text p:last-child { margin-top: 6px; }

  .actions { position: absolute; top: 501px; left: 0; width: 100%; display: flex; justify-content: center; gap: 8px; }
  .btn { display: inline-flex; align-items: center; justify-content: center; height: 20px;
    font-family: 'Poppins', sans-serif; font-size: 6.8px; text-decoration: none; background: var(--white); }
  .btn--dark { width: 81px; border: 1px solid var(--ink); color: var(--ink); }
  .btn--red { width: 88px; border: 1px solid var(--red); color: var(--red); }

  .footer { position: absolute; left: 0; width: 100%; background: var(--footer);
    color: var(--footer-text); font-family: 'Poppins', sans-serif; text-align: center; }
  .page--home .footer { top: 569px; height: 112px; }
  .page--focus .footer { top: 312px; height: 98px; }

  .social { display: flex; justify-content: center; gap: 5px; margin-top: 6px; }
  .social span { width: 14px; height: 14px; border: 1px solid var(--icon-ring); border-radius: 50%;
    background: #2d2d2d; }
  .contact { margin-top: 10px; font-size: 7.4px; display: flex; justify-content: center; gap: 9px; align-items: center; }
  .contact span { display: inline-flex; align-items: center; gap: 4px; }
  .contact svg { fill: var(--footer-text); }
  .links { margin-top: 8px; font-size: 7.4px; }
  .links a { color: var(--footer-text); text-decoration: none; }
  .links i { font-style: normal; margin: 0 4px; }
  .copyright { margin-top: 9px; font-size: 7.4px; }
</style>
</head>
<body>

<section class="page page--home">
  <div class="hero" role="img" aria-label="Dimmed photograph of a large warehouse interior with a blue technology overlay">
    <div class="brand"><span class="brand__dot"></span><span class="brand__name">Brisk.</span></div>
    <nav class="nav">
      <a href="#">HOME</a><a href="#">SOLUTIONS</a><a href="#">TESTIMONIAL LOGIN</a><a href="#">CONTACT US</a>
    </nav>
    <svg class="play" viewBox="0 0 36 36"><circle cx="18" cy="18" r="16.5" fill="#fff" stroke="#444" stroke-width="1"/><circle cx="18" cy="18" r="14" fill="none" stroke="#222" stroke-width="1.5"/><path d="M14.5 11.5 L24.5 18 L14.5 24.5 Z" fill="#222"/></svg>
    <svg class="slide-arrow slide-arrow--prev" width="14" height="26" viewBox="0 0 14 26"><path d="M12 1 L2 13 L12 25" fill="none" stroke="#fff" stroke-width="1"/></svg>
    <svg class="slide-arrow slide-arrow--next" width="14" height="26" viewBox="0 0 14 26"><path d="M2 1 L12 13 L2 25" fill="none" stroke="#fff" stroke-width="1"/></svg>
    <h1 class="hero__title">Brisk. Technology and Parcel Solutions Built<br>To Help Develop &amp; Manage Your Global Delivery Network</h1>
  </div>
  <svg class="wave" style="top:290px" height="20" viewBox="0 0 535 20"><path d="M0 18 H190 C220 18 235 4 267 4 C299 4 314 18 344 18 H535 V20 H0 Z" fill="#fff"/></svg>

  <div class="welcome">
    <div class="welcome__mark"></div>
    <h2 class="welcome__title">WELCOME TO <span>BRISK. TECHNOLOGY</span></h2>
    <div class="welcome__text">
      <p>Working closely with Ecommerce, Brisk. Technology have developed solutions purely focused on delivering what’s required within the global delivery marketplace. Meeting all needs and more for Retailers and Global Delivery Solution providers</p>
      <p>Allowing customers to grow at a fast pace; most importantly providing tools to help them manage their global delivery network supported by “Dynamic Real Time Visibility” management tools</p>
      <p>Ensuring solutions evolve to suit our customers business requirements</p>
    </div>
  </div>
  <div class="actions">
    <a class="btn btn--dark" href="#">BRISK PARCEL</a>
    <a class="btn btn--red" href="#">BRISK TECHNOLOGY</a>
  </div>

  <svg class="wave" style="top:553px" height="17" viewBox="0 0 535 17"><path d="M0 17 H200 C225 17 240 1 267 1 C294 1 309 17 334 17 H535 Z" fill="#222"/></svg>
  <footer class="footer">
    <div class="social"><span></span><span></span><span></span></div>
    <div class="contact">
      <span><svg width="7" height="7" viewBox="0 0 10 10"><path d="M2 0.5 L3.8 0.5 L4.5 3 L3.2 4 C3.8 5.3 4.7 6.2 6 6.8 L7 5.5 L9.5 6.2 L9.5 8 C9.5 9 8.7 9.5 8 9.5 C4 9.2 0.8 6 0.5 2 C0.5 1.2 1 0.5 2 0.5 Z"/></svg>555 0142 7788,</span>
      <span><svg width="6" height="8" viewBox="0 0 8 11"><path d="M4 0 C6.2 0 8 1.8 8 4 C8 6.5 4 11 4 11 C4 11 0 6.5 0 4 C0 1.8 1.8 0 4 0 Z M4 2.5 A1.5 1.5 0 1 0 4 5.5 A1.5 1.5 0 1 0 4 2.5 Z"/></svg>Unit 12 2nd Floor, PO Box – 4870,</span>
      <span><svg width="8" height="6" viewBox="0 0 10 8"><path d="M0.5 0.5 H9.5 V7.5 H0.5 Z M1.5 1.5 L5 4.3 L8.5 1.5" fill="none" stroke="#e6e6e6" stroke-width="1"/></svg>hello@brisktechnology.com</span>
    </div>
    <div class="links"><a href="#">Home</a><i>|</i><a href="#">About Us</a><i>|</i><a href="#">Solutions</a><i>|</i><a href="#">Testimonial Login</a><i>|</i><a href="#">Contact Us</a></div>
    <div class="copyright">Brisk Technology © 2018 All Rights Reserved.</div>
  </footer>
</section>

<section class="page page--focus">
  <div class="hero" role="img" aria-label="Dimmed photograph of a factory floor with warm orange lighting and a technology overlay">
    <div class="brand"><span class="brand__dot"></span><span class="brand__name">Brisk.</span></div>
    <svg class="play" viewBox="0 0 36 36"><circle cx="18" cy="18" r="16.5" fill="#fff" stroke="#444" stroke-width="1"/><circle cx="18" cy="18" r="14" fill="none" stroke="#222" stroke-width="1.5"/><path d="M14.5 11.5 L24.5 18 L14.5 24.5 Z" fill="#222"/></svg>
    <h1 class="hero__title">Brisk.Technology … Our Focus</h1>
    <div class="hero__copy">
      <p>We provide advanced software solutions to ensure you connect with global e commerce delivery carriers</p>
      <p>You can manage your Global Delivery Network in one place, with</p>
      <p>Our software will enable you monitor the productivity and reporting of your e commerce deliveries</p>
      <p>Manage your carriers, your delivery speeds, and your costs</p>
    </div>
  </div>
  <svg class="wave" style="top:298px" height="15" viewBox="0 0 535 15"><path d="M0 15 H200 C225 15 240 1 267 1 C294 1 309 15 334 15 H535 Z" fill="#222"/></svg>
  <footer class="footer">
    <div class="social"><span></span><span></span><span></span></div>
    <div class="contact">
      <span><svg width="7" height="7" viewBox="0 0 10 10"><path d="M2 0.5 L3.8 0.5 L4.5 3 L3.2 4 C3.8 5.3 4.7 6.2 6 6.8 L7 5.5 L9.5 6.2 L9.5 8 C9.5 9 8.7 9.5 8 9.5 C4 9.2 0.8 6 0.5 2 C0.5 1.2 1 0.5 2 0.5 Z"/></svg>555 0142 7788,</span>
      <span><svg width="6" height="8" viewBox="0 0 8 11"><path d="M4 0 C6.2 0 8 1.8 8 4 C8 6.5 4 11 4 11 C4 11 0 6.5 0 4 C0 1.8 1.8 0 4 0 Z M4 2.5 A1.5 1.5 0 1 0 4 5.5 A1.5 1.5 0 1 0 4 2.5 Z"/></svg>Unit 12 2nd Floor, PO Box – 4870,</span>
      <span><svg width="8" height="6" viewBox="0 0 10 8"><path d="M0.5 0.5 H9.5 V7.5 H0.5 Z M1.5 1.5 L5 4.3 L8.5 1.5" fill="none" stroke="#e6e6e6" stroke-width="1"/></svg>hello@brisktechnology.com</span>
    </div>
    <div class="links"><a href="#">Home</a><i>|</i><a href="#">About Us</a><i>|</i><a href="#">Solutions</a><i>|</i><a href="#">Testimonial Login</a><i>|</i><a href="#">Contact Us</a></div>
    <div class="copyright">Brisk Technology © 2018 All Rights Reserved.</div>
  </footer>
</section>

</body>
</html>
```